Zenqo - revolutionary mobile payment

The app is a P2P money trasfert, without the using of credit card or bank circuits it can transfer electronic money from one person to another consumers simply and immediatelly.
You can use the color you want, but the message we need to transert to consumer is simplicity, safety and coolness.
In attach the logo of the company and the wireframe of thre page of the app.
The goal is to design the page of the app with a clear, simple and intuitive graphic.
Updates

I have upgrade the brief with important information and detail, many thanks

Target Market(s)

all the people

Industry/Entity Type

Credit Card

Requirements
Must have
• You have to design one icon for each button in the first page, (shop is: where to shop)
in the second one a new intuitive image (instead of the hand) that let the user to understand that with a simple swipe he can process the payment
Nice to have
• You can include or esxclude what you want or belive can improve user experience of the app
Should not have
• too much color, too much button or information

```html
<!DOCTYPE html>
<html lang="it">
<head>
<meta charset="utf-8">
<title>Zenqo – mobile payment app screens</title>
<link rel="stylesheet" href="https://fonts.googleapis.com/css2?family=Open+Sans:wght@400;600;700&display=swap">
<style>
  :root {
    --page-bg: #e9e8ee;
    --status-bg: #0c0c0e;
    --topbar-bg: #f4f4f4;
    --navy: #2a3765;
    --navy-deep: #1f2a55;
    --plum: #5b3b63;
    --tile: rgba(38, 52, 98, 0.88);
    --tile-line: rgba(255, 255, 255, 0.18);
    --brand: #1f4f9a;
    --orange: #e8560f;
    --red: #c0262b;
    --green: #28a23e;
    --field: #e7e7e7;
    --amount: rgba(120, 128, 128, 0.75);
    --white: #ffffff;
    --ink: #1a1a1a;
  }
  * { box-sizing: border-box; margin: 0; padding: 0; }
  html, body { width: 1200px; height: 866px; overflow: hidden; }
  body {
    background: var(--page-bg);
    font-family: "Open Sans", sans-serif;
    position: relative;
  }
  .screen {
    position: absolute;
    top: 194px;
    width: 240px;
    height: 426px;
    transform: scale(1.128);
    transform-origin: 0 0;
    overflow: hidden;
    background: #999;
    box-shadow: 0 4px 18px rgba(0,0,0,.18);
  }
  .screen--home { left: 99px; }
  .screen--pay { left: 466px; }
  .screen--history { left: 827px; }

  .backdrop {
    position: absolute; inset: 0;
    background:
      radial-gradient(ellipse 60% 30% at 30% 52%, #b3283a 0%, transparent 70%),
      radial-gradient(ellipse 50% 25% at 75% 88%, #a91e2c 0%, transparent 70%),
      radial-gradient(ellipse 40% 30% at 80% 40%, #7c8588 0%, transparent 70%),
      radial-gradient(ellipse 50% 30% at 20% 85%, #6e2030 0%, transparent 70%),
      linear-gradient(180deg, #8a8f96 0%, #8c5a66 45%, #6d3340 100%);
  }

  .status-bar {
    position: absolute; top: 0; left: 0; right: 0; height: 20px;
    background: var(--status-bg); color: var(--white);
    font-size: 8.5px; font-weight: 600;
    display: flex; align-items: center; justify-content: space-between;
    padding: 0 6px;
  }
  .status-bar .carrier { display: flex; align-items: center; gap: 3px; }
  .status-bar .time { position: absolute; left: 0; right: 0; text-align: center; }
  .status-bar .battery { display: flex; align-items: center; gap: 3px; }
  .battery-icon { width: 17px; height: 7px; border: 1px solid var(--white); border-radius: 1px; position: relative; }
  .battery-icon::after { content: ""; position: absolute; left: 1px; top: 1px; width: 3px; height: 3px; background: var(--white); }

  .top-bar {
    position: absolute; top: 20px; left: 0; right: 0; height: 28px;
    background: var(--topbar-bg);
    display: flex; align-items: center; justify-content: space-between;
    padding: 0 6px;
  }
  .brand {
    display: flex; align-items: center; gap: 3px;
    font-size: 11px; font-weight: 700; color: var(--brand);
  }
  .brand-dot { width: 9px; height: 9px; border-radius: 50%; background: var(--brand); }

  .header {
    position: absolute; top: 48px; left: 0; right: 0; height: 84px;
    background: linear-gradient(110deg, var(--navy) 0%, #36406d 45%, var(--plum) 100%);
    color: var(--white);
  }
  .avatar {
    position: absolute; width: 54px; height: 54px; border-radius: 50%;
    background: radial-gradient(circle at 50% 40%, #b99a86 0%, #6f6a63 70%);
    border: 3px solid var(--white);
  }
  .back-panel {
    position: absolute; left: 0; top: 0; width: 48px; height: 100%;
    background: rgba(50, 70, 130, 0.75);
    font-size: 8.5px; display: flex; align-items: center; justify-content: center;
  }

  /* Home */
  .profile-name { position: absolute; left: 71px; top: 26px; font-size: 12.5px; font-weight: 600; }
  .profile-phone { position: absolute; left: 71px; top: 44px; font-size: 7.5px; }
  .edit-button {
    position: absolute; right: 8px; top: 33px; width: 17px; height: 17px;
    border-radius: 50%; background: var(--white);
    display: flex; align-items: center; justify-content: center;
  }
  .tile {
    position: absolute; width: 92px; height: 93px; background: var(--tile);
    color: var(--white); font-size: 10px; font-weight: 600;
    display: flex; flex-direction: column; align-items: center; justify-content: flex-end;
    padding-bottom: 8px; gap: 6px;
  }
  .tile svg { width: 50px; height: 50px; }
  .tile--pay { left: 19px; top: 173px; }
  .tile--ask { left: 129px; top: 173px; }
  .tile--account { left: 19px; top: 284px; }
  .tile--shop { left: 129px; top: 284px; }

  /* Pay */
  .pay-title {
    position: absolute; left: 108px; top: 24px;
    display: flex; align-items: center; gap: 5px;
    font-size: 17px; font-weight: 600;
  }
  .phone-field {
    position: absolute; left: 33px; top: 125px; width: 174px; height: 28px;
    background: var(--field); border: 1px solid #bbb;
    display: flex; align-items: center; font-size: 9px; color: var(--ink);
  }
  .phone-field .icon-box {
    width: 22px; height: 100%; background: var(--white); border-right: 1px solid #bbb;
    display: flex; align-items: center; justify-content: center;
  }
  .phone-field .prefix { font-weight: 700; margin: 0 4px 0 5px; }
  .euro-sign { position: absolute; left: 14px; top: 181px; color: var(--ink); font-size: 22px; font-weight: 700; }
  .amount-field {
    position: absolute; left: 38px; top: 173px; width: 188px; height: 43px;
    background: var(--amount); color: var(--ink);
    font-size: 21px; font-weight: 700; display: flex; align-items: center; justify-content: center;
  }
  .notes-select {
    position: absolute; left: 6px; top: 232px; width: 90px; height: 11px;
    background: rgba(60, 75, 120, 0.85); color: var(--white);
    font-size: 5.5px; display: flex; align-items: center; padding-left: 4px;
  }
  .keypad {
    position: absolute; left: 6px; top: 246px; width: 227px; height: 175px;
    display: grid; grid-template-columns: repeat(3, 1fr); grid-template-rows: repeat(4, 1fr);
    gap: 2px;
  }
  .key {
    background: var(--tile); color: var(--white);
    font-size: 17px; font-weight: 600;
    display: flex; align-items: center; justify-content: center;
  }
  .key--active { background: var(--orange); }

  /* History */
  .balance { position: absolute; right: 76px; top: 28px; text-align: right; }
  .balance-label { font-size: 9px; }
  .balance-amount { font-size: 14px; font-weight: 700; }
  .period-select {
    position: absolute; left: 169px; top: 136px; width: 66px; height: 12px;
    background: var(--navy-deep); color: var(--white); font-size: 5.5px;
    display: flex; align-items: center; justify-content: space-between; padding: 0 4px;
  }
  .transactions { position: absolute; left: 30px; top: 161px; width: 177px; list-style: none; }
  .transaction {
    height: 23px; margin-bottom: 6.6px;
    background: linear-gradient(90deg, #2e3f78, #3b4c88);
    border: 1px solid rgba(255,255,255,.25);
    color: var(--white); font-size: 7.5px;
    display: flex; align-items: center; padding: 0 5px;
  }
  .transaction .number { margin-left: 8px; width: 82px; }
  .transaction .value { font-weight: 700; flex: 1; }
  .action {
    position: absolute; top: 377px; width: 85px; height: 34px;
    color: var(--white); font-size: 10px; font-weight: 600;
    display: flex; align-items: center; justify-content: center;
  }
  .action--report { left: 28px; background: var(--red); }
  .action--pockets { left: 125px; background: var(--green); }
</style>
</head>
<body>

<!-- Home screen -->
<section class="screen screen--home">
  <div class="backdrop" role="img" aria-label="Soft blurred red and grey photographic background"></div>
  <div class="status-bar">
    <span class="carrier">●●●○○ NOVA</span>
    <span class="time">4:21 PM</span>
    <span class="battery">22% <span class="battery-icon"></span></span>
  </div>
  <div class="top-bar">
    <svg width="16" height="16" viewBox="0 0 16 16" aria-label="Settings"><circle cx="7" cy="9" r="4" fill="none" stroke="#333" stroke-width="2.5" stroke-dasharray="2 1.2"/><circle cx="12.5" cy="3.5" r="2" fill="none" stroke="#333" stroke-width="1.5"/></svg>
    <span class="brand"><span class="brand-dot"></span>Zenqo</span>
  </div>
  <header class="header">
    <div class="avatar" role="img" aria-label="User profile photo" style="left:8px; top:14px;"></div>
    <div class="profile-name">Marco Vellani</div>
    <div class="profile-phone">+39 300 555 0142</div>
    <div class="edit-button"><svg width="9" height="9" viewBox="0 0 10 10"><path d="M2 8 L7.5 2.5 L8.5 3.5 L3 9 L1.5 9.5 Z" fill="#333"/></svg></div>
  </header>
  <a class="tile tile--pay">
    <svg viewBox="0 0 50 50"><rect x="12" y="20" width="32" height="20" rx="2" fill="#fff"/><rect x="12" y="24" width="32" height="4" fill="#2a3765"/><text x="36" y="38" font-size="9" font-weight="700" fill="#2a3765" font-family="Open Sans, sans-serif">€</text><path d="M4 12 L16 24 L12 30 L2 22 Z" fill="#fff"/></svg>
    Pay
  </a>
  <a class="tile tile--ask">
    <svg viewBox="0 0 50 50"><path d="M8 22 L25 36 L42 22 L42 44 L8 44 Z" fill="#fff"/><path d="M20 4 H30 V14 H36 L25 26 L14 14 H20 Z" fill="#fff"/><rect x="30" y="26" width="14" height="14" fill="#fff" stroke="#2a3765"/><text x="33" y="37" font-size="10" font-weight="700" fill="#2a3765" font-family="Open Sans, sans-serif">€</text></svg>
    Ask
  </a>
  <a class="tile tile--account">
    <svg viewBox="0 0 50 50"><circle cx="25" cy="14" r="9" fill="#fff"/><path d="M8 46 C8 30 16 26 25 26 C34 26 42 30 42 46 Z" fill="#fff"/><path d="M23 27 L25 40 L27 27 Z" fill="#2a3765"/></svg>
    Account
  </a>
  <a class="tile tile--shop">
    <svg viewBox="0 0 50 50"><path d="M4 12 L16 6 L34 12 L46 6 V40 L34 46 L16 40 L4 46 Z" fill="none" stroke="#fff" stroke-width="3"/><path d="M30 6 C24 6 21 11 23 16 L30 28 L37 16 C39 11 36 6 30 6 Z" fill="#fff"/><circle cx="30" cy="13" r="3" fill="#2a3765"/></svg>
    Shop
  </a>
</section>

<!-- Pay screen -->
<section class="screen screen--pay">
  <div class="backdrop" role="img" aria-label="Soft blurred red and grey photographic background"></div>
  <div class="status-bar">
    <span class="carrier">●●●○○ NOVA</span>
    <span class="time">4:21 PM</span>
    <span class="battery">22% <span class="battery-icon"></span></span>
  </div>
  <div class="top-bar">
    <svg width="16" height="16" viewBox="0 0 16 16" aria-label="Settings"><circle cx="7" cy="9" r="4" fill="none" stroke="#333" stroke-width="2.5" stroke-dasharray="2 1.2"/><circle cx="12.5" cy="3.5" r="2" fill="none" stroke="#333" stroke-width="1.5"/></svg>
    <span class="brand"><span class="brand-dot"></span>Zenqo</span>
  </div>
  <header class="header" style="height:52px;">
    <div class="back-panel">‹ Indietro</div>
    <div class="pay-title">
      <svg width="22" height="22" viewBox="0 0 22 22"><path d="M9 20 V8 a2 2 0 0 1 4 0 V13 h3 a3 3 0 0 1 3 3 V20 Z" fill="#fff"/><path d="M4 6 H18 M15 3 L18 6 L15 9" stroke="#fff" stroke-width="1.8" fill="none"/></svg>
      Pay
    </div>
  </header>
  <div class="phone-field">
    <span class="icon-box"><svg width="10" height="16" viewBox="0 0 10 16"><rect x="1" y="1" width="8" height="14" rx="1.5" fill="none" stroke="#111" stroke-width="1.5"/><rect x="2.5" y="3" width="5" height="8" fill="#111"/></svg></span>
    <span class="prefix">+39</span> Cellulare
  </div>
  <div class="euro-sign">€</div>
  <div class="amount-field">851.33</div>
  <div class="notes-select">Inserisci note (opzionale) ▾</div>
  <div class="keypad">
    <span class="key">1</span><span class="key">2</span><span class="key">3</span>
    <span class="key">4</span><span class="key">5</span><span class="key">6</span>
    <span class="key">7</span><span class="key key--active">8</span><span class="key">9</span>
    <span class="key">.</span><span class="key">0</span>
    <span class="key"><svg width="18" height="12" viewBox="0 0 18 12"><path d="M5 0 H18 V12 H5 L0 6 Z" fill="#fff"/><path d="M9 3 L14 9 M14 3 L9 9" stroke="#2a3765" stroke-width="1.6"/></svg></span>
  </div>
</section>

<!-- History screen -->
<section class="screen screen--history">
  <div class="backdrop" role="img" aria-label="Soft blurred red and grey photographic background"></div>
  <div class="status-bar">
    <span class="carrier">●●●○○ NOVA</span>
    <span class="time">4:21 PM</span>
    <span class="battery">22% <span class="battery-icon"></span></span>
  </div>
  <div class="top-bar">
    <svg width="16" height="16" viewBox="0 0 16 16" aria-label="Settings"><circle cx="7" cy="9" r="4" fill="none" stroke="#333" stroke-width="2.5" stroke-dasharray="2 1.2"/><circle cx="12.5" cy="3.5" r="2" fill="none" stroke="#333" stroke-width="1.5"/></svg>
    <span class="brand"><span class="brand-dot"></span>Zenqo</span>
  </div>
  <header class="header">
    <div class="back-panel">‹ Indietro</div>
    <div class="balance">
      <div class="balance-label">Il Tuo Saldo</div>
      <div class="balance-amount">€106.82</div>
    </div>
    <div class="avatar" role="img" aria-label="User profile photo" style="left:175px; top:14px;"></div>
  </header>
  <div class="period-select"><span>Ultimi 30 Giorni</span><span>⌄</span></div>
  <ul class="transactions">
    <li class="transaction"><svg width="11" height="10" viewBox="0 0 11 10"><path d="M5.5 0 L11 5 H9 V10 H2 V5 H0 Z" fill="#fff"/></svg><span class="number">+39 310 555 0187</span><span class="value">€ 1</span>▶</li>
    <li class="transaction"><svg width="11" height="10" viewBox="0 0 11 10"><path d="M5.5 0 L11 5 H9 V10 H2 V5 H0 Z" fill="#fff"/></svg><span class="number">+39 310 555 0187</span><span class="value">€ -1</span>▶</li>
    <li class="transaction"><svg width="11" height="10" viewBox="0 0 11 10"><path d="M5.5 0 L11 5 H9 V10 H2 V5 H0 Z" fill="#fff"/></svg><span class="number">+39 020 555 0163</span><span class="value">€ 200</span>▶</li>
    <li class="transaction"><svg width="11" height="10" viewBox="0 0 11 10"><path d="M5.5 0 L11 5 H9 V10 H2 V5 H0 Z" fill="#fff"/></svg><span class="number">+39 055 555 0119</span><span class="value">€ 12</span>▶</li>
    <li class="transaction"><svg width="11" height="10" viewBox="0 0 11 10"><path d="M5.5 0 L11 5 H9 V10 H2 V5 H0 Z" fill="#fff"/></svg><span class="number">+39 310 555 0187</span><span class="value">€ -1</span>▶</li>
    <li class="transaction"><svg width="11" height="10" viewBox="0 0 11 10"><path d="M5.5 0 L11 5 H9 V10 H2 V5 H0 Z" fill="#fff"/></svg><span class="number">+39 020 555 0163</span><span class="value">€ 200</span>▶</li>
    <li class="transaction"><svg width="11" height="10" viewBox="0 0 11 10"><path d="M5.5 0 L11 5 H9 V10 H2 V5 H0 Z" fill="#fff"/></svg><span class="number">+39 055 555 0119</span><span class="value">€ 12</span>▶</li>
  </ul>
  <a class="action action--report">Report</a>
  <a class="action action--pockets">Tasche</a>
</section>

</body>
</html>
```